Create Social Media design templates for Online-Education-Startup

We are an online platform for pupils who provide group courses and on demand individual tutroing lessons. Our core values are personalisation, family and success. We need a holistic social media design concept which includes nine possible layouts for Instagram posts which reflect our values and promote not only our offerings and special deals but also support in building our brand image (for example: telling company history, daily news, funny facts, getting to know the team etc.).
Additionally, we need design elements for our YouTube channel:
-Videocover
-Cover Image for the channel

Our main colour is orange (RGB-Code: 255;105;31) and additional colours white, black, and grey. For the reference have a look at our website: www.lernvolta.de.

Target Market(s)

We want to attract customers to our online tutoring courses and build a brand.

Industry/Entity Type

Education / Tutoring

Font styles to use
Sans Serif

Requirements
Must have
• Familiarize yourself with the style of our website. The designs should fit as well as possible.

```html
<!DOCTYPE html>
<html lang="de">
<head>
<meta charset="utf-8">
<title>Lernvolta – Nachhilfe-Konzept</title>
<link rel="stylesheet" href="https://fonts.googleapis.com/css2?family=Inter:wght@400;700;800&display=swap">
<style>
  :root {
    --orange: #ff6920;
    --paper: #fafafa;
    --ink: #111111;
    --body: #333333;
    --white: #ffffff;
  }
  html, body {
    margin: 0;
    width: 1200px;
    height: 1200px;
    overflow: hidden;
    background: var(--paper);
    font-family: "Inter", Arial, sans-serif;
  }
  .post {
    position: relative;
    width: 1200px;
    height: 1200px;
    overflow: hidden;
    background: var(--paper);
  }
  .backdrop {
    position: absolute;
    inset: 0;
  }
  .brand {
    position: absolute;
    left: 79px;
    top: 60px;
    display: flex;
    align-items: center;
    gap: 26px;
  }
  .brand-mark {
    width: 206px;
    height: 176px;
    border: 10px solid var(--orange);
    border-radius: 50%;
    box-sizing: border-box;
  }
  .brand-text {
    color: var(--ink);
    line-height: 1.25;
  }
  .brand-name {
    font-size: 56px;
    font-weight: 700;
    letter-spacing: -0.5px;
    margin: 0;
  }
  .brand-sub {
    font-size: 52px;
    font-weight: 400;
    margin: 0;
  }
  .headline {
    position: absolute;
    left: 81px;
    top: 285px;
    margin: 0;
    color: var(--orange);
    font-size: 53px;
    font-weight: 800;
    line-height: 59px;
    letter-spacing: -0.3px;
  }
  .steps {
    position: absolute;
    left: 83px;
    top: 430px;
    width: 560px;
    color: var(--body);
    font-size: 24.5px;
    line-height: 31px;
    letter-spacing: 0.4px;
  }
  .step { margin: 0 0 22px; }
  .step-label, .step-title {
    display: block;
    font-weight: 700;
    letter-spacing: 0;
  }
  .step p { margin: 0; }
  .contact {
    position: absolute;
    left: 66px;
    top: 1068px;
    color: var(--white);
    font-weight: 800;
  }
  .contact-phone { font-size: 35px; line-height: 46px; margin: 0; }
  .contact-web { font-size: 46px; line-height: 52px; margin: 0; }
</style>
</head>
<body>
<main class="post">
  <svg class="backdrop" width="1200" height="1200" viewBox="0 0 1200 1200">
    <defs>
      <linearGradient id="photoBase" x1="0" y1="0" x2="1" y2="0">
        <stop offset="0" stop-color="#fafafa" stop-opacity="0"/>
        <stop offset="0.4" stop-color="#eeeef0" stop-opacity="0.7"/>
        <stop offset="0.75" stop-color="#dcdce0"/>
        <stop offset="1" stop-color="#d2d2d6"/>
      </linearGradient>
      <radialGradient id="photoFigure" cx="1010" cy="820" r="260" gradientUnits="userSpaceOnUse">
        <stop offset="0" stop-color="#6d7592" stop-opacity="0.45"/>
        <stop offset="1" stop-color="#6d7592" stop-opacity="0"/>
      </radialGradient>
      <radialGradient id="photoDesk" cx="900" cy="1080" r="320" gradientUnits="userSpaceOnUse">
        <stop offset="0" stop-color="#f1e4dc" stop-opacity="0.8"/>
        <stop offset="1" stop-color="#f1e4dc" stop-opacity="0"/>
      </radialGradient>
      <linearGradient id="photoFade" x1="0" y1="0" x2="0" y2="1">
        <stop offset="0" stop-color="#fafafa" stop-opacity="0.9"/>
        <stop offset="0.25" stop-color="#fafafa" stop-opacity="0"/>
      </linearGradient>
    </defs>
    <g role="img" aria-label="Foto: ein lächelndes Mädchen lernt mit Stift, Heft und Laptop am Schreibtisch">
      <path d="M246 435 H1200 V1025 C1100 1110 960 1140 856 1132 C560 1110 380 1030 246 960 Z" fill="url(#photoBase)"/>
      <path d="M246 435 H1200 V1025 C1100 1110 960 1140 856 1132 C560 1110 380 1030 246 960 Z" fill="url(#photoFigure)"/>
      <path d="M246 435 H1200 V1025 C1100 1110 960 1140 856 1132 C560 1110 380 1030 246 960 Z" fill="url(#photoDesk)"/>
      <path d="M246 435 H1200 V1025 C1100 1110 960 1140 856 1132 C560 1110 380 1030 246 960 Z" fill="url(#photoFade)"/>
    </g>
    <path class="corner-top-left" d="M0 0 H196 C130 25 60 60 0 96 Z" fill="var(--orange)"/>
    <path class="corner-top-right" d="M825 0 H1200 V304 C1080 160 960 75 825 0 Z" fill="var(--orange)"/>
    <path class="band-bottom" d="M0 759 C250 990 560 1110 856 1132 C960 1140 1100 1110 1200 1025 V1200 H0 Z" fill="var(--orange)"/>
  </svg>

  <header class="brand">
    <div class="brand-mark" aria-hidden="true"></div>
    <div class="brand-text">
      <p class="brand-name">Lernvolta</p>
      <p class="brand-sub">Bildungsinstitut</p>
    </div>
  </header>

  <h1 class="headline">Unser Nachhilfe-Konzept bereitet<br>Dich Schritt für Schritt auf Dein Ziel vor.</h1>

  <section class="steps">
    <div class="step">
      <span class="step-label">1. Schritt</span>
      <span class="step-title">Wöchentliche Online-Nachhilfe</span>
      <p>Online-Gruppenkurse zur zielgerichteten<br>Vorbereitung auf Prüfungen und Abschlüsse<br>bilden dabei die Grundlage unseres<br>Nachhilfe-Konzept</p>
    </div>
    <div class="step">
      <span class="step-label">2. Schritt</span>
      <span class="step-title">Gemeinsam zum Schulerfolg</span>
      <p>Die Synergie-Effekte zwischen den<br>Kursteilnehmenden ermöglichen besonders<br>positive Ergebnisse und das Lernen passiert<br>wie von allein.</p>
    </div>
  </section>

  <footer class="contact">
    <p class="contact-phone">CALL: 089 55501234</p>
    <p class="contact-web">https://lernvolta.de/</p>
  </footer>
</main>
</body>
</html>
```